Business card for Luxury Portable Restroom Trailer company

We are a Luxury Portable Restroom Trailer Company Called FALCRIDGE HIRES. Based in Orange County California. We provide portable restroom trailers for events, such as, Weddings, Concerts, Charity events, Sporting events, Tournaments, Corporate events, ect. We rent and Sell the Luxury restrooms. Our colors are white, grey, and Orange. As you will see in the logo we uploaded.
There are 2 people in the company so the names and titles will change for the 3 people but card will remain the same. Here is the information for each Person: Dwight Penner CFO 555 318-0476
next Person: Leon Marchetti VP 555 318-0476
Next Person: Owen Marchetti CEO 555 318-0476
Information to include on the card: Luxury Restroom Trailers Rental and Sales. Weddings, Concerts, Charity, Sporting and Corp. Events.

```html
<!DOCTYPE html>
<html lang="en">
<head>
<meta charset="utf-8">
<title>Falcridge Hires – Business Card</title>
<link rel="stylesheet" href="https://fonts.googleapis.com/css2?family=Montserrat:wght@500;600;800&display=swap">
<style>
  :root {
    --orange: #f16f24;
    --grey: #58595b;
    --ink: #1d1d1d;
    --white: #ffffff;
    --backdrop: #e6e6e6;
  }
  * { box-sizing: border-box; margin: 0; padding: 0; }
  html, body { width: 1200px; height: 960px; overflow: hidden; }
  body {
    background: var(--backdrop);
    font-family: "Montserrat", Arial, sans-serif;
    position: relative;
  }
  .card {
    position: absolute;
    left: 210px;
    width: 780px;
    height: 446px;
    border-radius: 24px;
    overflow: hidden;
    box-shadow: 0 6px 18px rgba(0,0,0,0.18);
  }
  .card--front { top: 22px; background: var(--orange); color: var(--white); }
  .card--back { top: 492px; background: var(--white); }

  .brand {
    display: flex;
    align-items: center;
    gap: 16px;
    font-weight: 800;
    letter-spacing: 2px;
    text-transform: uppercase;
    white-space: nowrap;
  }
  .brand__square { width: 22px; height: 22px; }

  .card--front .brand {
    position: absolute;
    left: 0; right: 0; top: 120px;
    justify-content: center;
    font-size: 60px;
  }
  .card--front .brand__square { background: var(--white); width: 30px; height: 30px; }

  .services {
    position: absolute;
    left: 0; right: 0; top: 290px;
    text-align: center;
    font-weight: 500;
    font-size: 20px;
    line-height: 40px;
  }
  .services .dot {
    display: inline-block;
    width: 11px; height: 11px;
    border-radius: 50%;
    background: var(--white);
    margin: 0 8px 2px 14px;
  }

  .card--back .brand {
    position: absolute;
    left: 44px; top: 150px;
    font-size: 31px;
    color: var(--grey);
  }
  .card--back .brand__square { background: var(--orange); }

  .divider {
    position: absolute;
    left: 428px; top: 58px;
    width: 2px; height: 210px;
    background: var(--orange);
  }
  .contacts {
    position: absolute;
    left: 452px; top: 40px;
    display: flex;
    flex-direction: column;
    gap: 12px;
  }
  .contact__name {
    color: var(--orange);
    font-weight: 800;
    font-size: 21px;
    text-transform: uppercase;
    letter-spacing: 0.5px;
    line-height: 24px;
  }
  .contact__title, .contact__phone {
    color: var(--ink);
    font-weight: 500;
    font-size: 15px;
    line-height: 20px;
  }
  .contact__phone { display: flex; align-items: center; gap: 8px; }
  .contact__phone svg { width: 16px; height: 16px; fill: var(--orange); }

  .wave { position: absolute; left: 0; bottom: 0; width: 780px; height: 446px; }
</style>
</head>
<body>

<section class="card card--front" aria-label="Card front">
  <div class="brand"><span class="brand__square"></span>Falcridge Hires</div>
  <p class="services">
    <span class="dot"></span>Luxury Restroom Trailers Rental and Sales<br>
    <span class="dot"></span>Weddings <span class="dot"></span>Concerts <span class="dot"></span>Charity <span class="dot"></span>Sporting and Corp <span class="dot"></span>Events
  </p>
</section>

<section class="card card--back" aria-label="Card back">
  <svg class="wave" viewBox="0 0 780 446" aria-hidden="true">
    <path d="M0,424 C260,418 440,360 560,318 C650,288 710,280 780,278 L780,290 C710,292 650,300 560,330 C440,372 260,428 0,432 Z" fill="var(--grey)"/>
    <path d="M0,436 C260,432 440,376 560,336 C650,306 710,298 780,296 L780,446 L0,446 Z" fill="var(--orange)"/>
  </svg>

  <div class="brand"><span class="brand__square"></span>Falcridge Hires</div>
  <div class="divider"></div>

  <div class="contacts">
    <div class="contact">
      <p class="contact__name">Dwight Penner</p>
      <p class="contact__title">CFO</p>
      <p class="contact__phone"><svg viewBox="0 0 24 24"><path d="M6.6 10.8a15 15 0 0 0 6.6 6.6l2.2-2.2a1 1 0 0 1 1-.25 11.4 11.4 0 0 0 3.6.57 1 1 0 0 1 1 1V20a1 1 0 0 1-1 1A17 17 0 0 1 3 4a1 1 0 0 1 1-1h3.5a1 1 0 0 1 1 1c0 1.25.2 2.45.57 3.57a1 1 0 0 1-.25 1z"/></svg>555 318-0476</p>
    </div>
    <div class="contact">
      <p class="contact__name">Leon Marchetti</p>
      <p class="contact__title">VP</p>
      <p class="contact__phone"><svg viewBox="0 0 24 24"><path d="M6.6 10.8a15 15 0 0 0 6.6 6.6l2.2-2.2a1 1 0 0 1 1-.25 11.4 11.4 0 0 0 3.6.57 1 1 0 0 1 1 1V20a1 1 0 0 1-1 1A17 17 0 0 1 3 4a1 1 0 0 1 1-1h3.5a1 1 0 0 1 1 1c0 1.25.2 2.45.57 3.57a1 1 0 0 1-.25 1z"/></svg>555 318-0476</p>
    </div>
    <div class="contact">
      <p class="contact__name">Owen Marchetti</p>
      <p class="contact__title">CEO</p>
      <p class="contact__phone"><svg viewBox="0 0 24 24"><path d="M6.6 10.8a15 15 0 0 0 6.6 6.6l2.2-2.2a1 1 0 0 1 1-.25 11.4 11.4 0 0 0 3.6.57 1 1 0 0 1 1 1V20a1 1 0 0 1-1 1A17 17 0 0 1 3 4a1 1 0 0 1 1-1h3.5a1 1 0 0 1 1 1c0 1.25.2 2.45.57 3.57a1 1 0 0 1-.25 1z"/></svg>555 318-0476</p>
    </div>
  </div>
</section>

</body>
</html>
```